4D Cradle Glimpse Luxury Ultrasound Billboard

Design a HIGH-END, MODERN billboard for my private prenatal ultrasound studio, 4D Cradle Glimpse, located in Pace, Florida.
This billboard will be viewed by drivers traveling at highway speeds, so it must be extremely clean, simple, and readable within 6 seconds.
About My Business
4D Cradle Glimpse is a private prenatal ultrasound studio specializing in:
Highest technology 4D/HD Ultrasounds
Early Gender Determination
Pregnancy Confirmation
I have been serving families for nearly 10 years and is known for creating a memorable experience, not just an ultrasound appointment.
Design Style
I DO NOT want:
Flowers
Leaves
Swirls
Glitter
Hearts everywhere
Busy backgrounds
Generic maternity stock graphics
I DO want:
Modern
Luxury
Upscale
Clean
Professional
Eye-catching
Premium medical spa feel
Colors
Use colors from my logo:
LOGO Green ( or a deep green)
Black
White
Soft Gold accents
Images:
Incorporate my professional headshot in a clean, modern way, logo, and the ultrasound images
Text
Keep wording minimal.
Primary Headline ( OPEN TO IDEAS) :
EXAMPLES ( WOULD RATHER SOMETHING MORE CATCHY)
" ADVANCED IMAGING. UNFORGETTABLE MOMENTS"
"MEET YOUR BABY BEFORE BIRTH"
Under headline:
4D Ultrasound • Early Gender • Pregnancy Confirmation
Business Name:
4D Cradle Glimpse
Private Prenatal Ultrasound Studio
Phone Number:
850-471-5923
Important
This billboard must be readable in 5–6 seconds from a moving vehicle.
Less text is better.
The phone number and business name must be visible from a distance.
The design should feel like a premium brand that immediately tells expecting parents:
“This is where I go to see my baby.”
Files Provided
Official logo
Headshot
Ultrasound images
Don’t make this look like a medical office billboard.
Make it look like a luxury baby experience billboard. That’s what separates 4D Cradle Glimpse from hospitals, OB offices, and all the new studios popping up around you. The emotional connection is what gets moms to book. ❤️
Billboard Size - 10.6” x 36”

```html
<!DOCTYPE html>
<html lang="en">
<head>
<meta charset="utf-8">
<title>4D Cradle Glimpse Billboard</title>
<link href="https://fonts.googleapis.com/css2?family=Poppins:wght@700;800&family=Oswald:wght@500&display=swap" rel="stylesheet">
<style>
  :root{
    --stage:#8a8a8a;
    --black:#000;
    --white:#fff;
    --gold:#c9a03a;
    --gold-deep:#b08a2c;
    --ink:#0a0a0a;
    --slate:#5d6662;
  }
  *{margin:0;padding:0;box-sizing:border-box}
  html,body{width:1200px;height:605px;overflow:hidden;background:var(--stage)}
  .billboard{position:absolute;left:48px;top:142px;width:1104px;height:322px;background:var(--white);overflow:hidden;box-shadow:0 6px 18px rgba(0,0,0,.35)}
  .billboard__top{position:absolute;left:0;top:0;width:100%;height:185px;background:var(--black)}
  .brand{position:absolute;left:61px;top:28px;width:200px;height:100px;border:2px solid var(--slate);border-radius:10px;display:flex;align-items:center;justify-content:center;gap:7px}
  .brand__dot{width:12px;height:12px;border-radius:50%;background:var(--gold);flex:none}
  .brand__name{font-family:"Poppins",sans-serif;font-weight:700;font-size:18px;line-height:1.1;color:var(--gold);text-align:center}
  .brand__tagline{position:absolute;left:61px;top:136px;width:200px;text-align:center;white-space:nowrap;font-family:"Oswald",sans-serif;font-weight:500;font-size:11.5px;line-height:16px;color:var(--white);letter-spacing:-.1px}
  .headline{position:absolute;left:284px;top:22px;font-family:"Poppins",sans-serif;font-weight:800;font-size:72px;line-height:64px;letter-spacing:-1px;white-space:nowrap}
  .headline__gold{color:var(--gold);display:block}
  .headline__white{color:var(--white);display:block}
  .services{position:absolute;left:183px;top:167px;width:740px;height:40px;display:flex;list-style:none;background:var(--gold)}
  .service{display:flex;align-items:center;gap:6px;height:40px;font-family:"Oswald",sans-serif;font-weight:500;font-size:24px;line-height:1;color:var(--white);white-space:nowrap}
  .service--ultrasound{width:249px;padding-left:63px}
  .service--gender{width:180px;padding-left:9px;background:var(--gold-deep)}
  .service--confirmation{width:311px;padding-left:9px}
  .service__dot{width:10px;height:10px;border-radius:50%;background:var(--slate);flex:none}
  .phone{position:absolute;left:284px;top:216px;font-family:"Poppins",sans-serif;font-weight:800;font-size:86px;line-height:90px;color:var(--ink);letter-spacing:-1px;white-space:nowrap}
  .headshot{position:absolute;left:66px;top:167px;width:189px;height:189px;border-radius:50%;border:3px solid var(--black);background:radial-gradient(circle at 50% 40%,#e8e2d8 0%,#b9b1a4 45%,#3d4a3c 100%)}
  .mom-photo{position:absolute;left:924px;top:0;width:172px;height:322px;background:linear-gradient(180deg,#c79a6a 0%,#e7a92c 25%,#e9ad2a 70%,#d99a1e 100%);border-radius:60px 30px 0 0}
</style>
</head>
<body>
  <main class="billboard">
    <div class="billboard__top"></div>

    <div class="brand">
      <span class="brand__dot"></span>
      <span class="brand__name">4D Cradle Glimpse</span>
    </div>
    <p class="brand__tagline">PRIVATE PRENATAL ULTRASOUND STUDIO</p>

    <h1 class="headline">
      <span class="headline__gold">MEET YOUR BABY</span>
      <span class="headline__white">BEFORE BIRTH</span>
    </h1>

    <ul class="services">
      <li class="service service--ultrasound"><span class="service__dot"></span>4D ULTRASOUND</li>
      <li class="service service--gender"><span class="service__dot"></span>EARLY GENDER</li>
      <li class="service service--confirmation"><span class="service__dot"></span>PREGNANCY CONFIRMATION</li>
    </ul>

    <p class="phone">850-471-5923</p>

    <div class="headshot" role="img" aria-label="Professional headshot of the studio owner beside ultrasound equipment"></div>
    <div class="mom-photo" role="img" aria-label="Expecting mother in a yellow dress holding an ultrasound print against her belly"></div>
  </main>
</body>
</html>
```